Leading Financial Advisory Firm Needs a Web Redesign

Job Type
Web Redesign

Task Outline
Create an Updated Web Design for our existing web site

Task Description
Dunmore Kestrel Group Inc. is a leading financial advisory firm to the global steel, metals and mining sectors. We are seeking a web designer to refashion, freshen and update the look of our existing website. The substance of the revised website should reflect our updated Credentials attached.

Our existing web site has an outdated “look”; it was originally put together quickly from an earlier PowerPoint presentation of our Credentials. We do not want the revised web site to look like a PowerPoint presentation which has been put up online. Rather, with a designer’s help, we would like to refashion the pages so that the look and feel of the site is consistent with a professional service organization's site. We are not interested in any significant changes in substance, just in format. There should also be no changes to the design/font/color of the “Dunmore Kestrel” logo.

The final selected designer will be responsible for all design and coding/programming responsibilities subject to our approval. The revised site should be done in Word Press or similar "user-friendly" application so that we can make edits afterwards.

A few specific changes:
• Textual changes:
• Wherever it currently says Dunmore Kestrel is an “affiliate” of Orvanne, this should be replaced with “Broker Dealer related services provided through Orvanne Partners LLC”; this appears on the copyright info on the bottom of each page;
• Please also add this telephone number to the 212 number listed: 917-555-0183;
• The text on the “About Us” tab needs to be updated as follows: “We currently have active steel, metals and mining assignments in Europe, South Africa, Australia and Ukraine.”
• The Services tab under Core Services currently says “Capital Raising (through affiliates)”; it should say “Capital Raising (through broker dealers)”;
• Our firm name in the Contacts tab should be “Dunmore Kestrel Group Inc.”
• Tara Wendle’ bio should be removed from the Bios tab;
• The map in the Global Scope and Perspective tab should be replaced with the map in the attached updated Credentials (see slide 11)

Very truly yours,

Dunmore Kestrel Group Inc.

Our current website is: http://www.dunmorekestrel.example

Deadline
5 Days

Target Market(s)
Companies in the steel, metals and mining sectors interested in financial advisory services and/or strategic and/or financial partners.

Industry/Entity Type

Financial

```html
<!DOCTYPE html>
<html lang="en">
<head>
<meta charset="utf-8">
<title>Dunmore Kestrel — Financial Advisors to Steel, Metals and Mining</title>
<link rel="stylesheet" href="https://fonts.googleapis.com/css2?family=Open+Sans:ital,wght@0,400;0,600;0,700;1,600&display=swap">
<style>
  :root {
    --green: #1f6a1b;
    --green-dark: #0f5212;
    --btn: #0f5a0f;
    --ink: #222;
    --text: #444;
    --panel: #efeeef;
    --rule: #dedede;
    --white: #fff;
  }
  * { margin: 0; padding: 0; box-sizing: border-box; }
  html, body { width: 865px; height: 1200px; overflow: hidden; background: var(--white); }
  body { position: relative; font-family: "Open Sans", Arial, sans-serif; color: var(--text); }
  .abs { position: absolute; }

  .brand { left: 138px; top: 19px; }
  .brand-name { font-size: 19px; font-weight: 700; color: var(--green); letter-spacing: .5px; line-height: 1.1; }
  .phone { left: 647px; top: 22px; display: flex; align-items: center; gap: 8px; font-size: 9px; color: var(--ink); }

  .nav { left: 0; top: 57px; width: 865px; height: 27px; background: var(--green); }
  .nav ul { list-style: none; display: flex; position: absolute; left: 138px; top: 0; height: 27px; align-items: center; }
  .nav li { font-size: 7.6px; font-weight: 600; color: var(--white); margin-right: 21px; }

  .hero { left: 122px; top: 101px; width: 620px; height: 250px;
    background: radial-gradient(circle at 32% 28%, #f3e8d8 0%, #b9a48c 18%, #6d5a48 42%, #2e2620 75%, #1a1512 100%); }
  .hero-caption { left: 478px; top: 153px; width: 250px; font-size: 11.5px; font-style: italic; font-weight: 600; color: var(--white); line-height: 1.85; }
  .hero-dots { left: 697px; top: 335px; display: flex; gap: 4px; }
  .hero-dots span { width: 6px; height: 6px; border-radius: 50%; background: #eee; }
  .hero-dots span:first-child { background: var(--green); }

  .h2 { font-size: 12px; font-weight: 600; color: var(--ink); }
  .h2 em { font-style: normal; color: var(--green); }

  .welcome { left: 122px; top: 369px; width: 620px; height: 161px; background: var(--panel); }
  .welcome .h2 { position: absolute; left: 17px; top: 11px; }
  .welcome-photo { left: 16px; top: 40px; width: 110px; height: 94px; background: linear-gradient(180deg, #cfd5db, #8b98a6 55%, #2d3238); }
  .welcome-rule { left: 150px; top: 40px; width: 1px; height: 90px; background: #d8d6d8; }
  .welcome-text { left: 166px; top: 33px; width: 445px; font-size: 7.3px; line-height: 12.4px; color: var(--text); }

  .services-title { left: 136px; top: 554px; }
  .services-copy { left: 136px; top: 580px; width: 340px; font-size: 7.3px; line-height: 12.4px; }
  .services-list { left: 136px; top: 643px; list-style: none; }
  .services-list li { display: flex; align-items: center; gap: 8px; font-size: 7.3px; height: 19.7px; color: #333; }
  .services-photo { left: 501px; top: 582px; width: 208px; height: 138px; background: linear-gradient(160deg, #c9d3dd, #7c90a6 45%, #3b4a5c 80%, #c9b28c); }
  .btn { display: inline-block; background: var(--btn); color: var(--white); font-size: 7.6px; padding: 3px 6px; border: 1px solid #0a3d0a; }

  .divider { left: 122px; top: 766px; width: 620px; height: 1px; background: var(--rule); }

  .articles-title { left: 136px; top: 786px; }
  .article { left: 136px; width: 205px; }
  .article h3 { font-size: 8.6px; font-weight: 600; color: var(--green); }
  .article .date { font-size: 7px; color: var(--green); margin-top: 3px; }
  .article p { font-size: 7.2px; line-height: 12.4px; text-align: justify; margin-top: 6px; }
  .dots { left: 136px; top: 890px; width: 197px; border-top: 1px dotted #bbb; }

  .approach-title { left: 402px; top: 786px; }
  .approach { left: 400px; width: 340px; list-style: none; font-size: 7.2px; line-height: 12.3px; }
  .approach li { position: relative; padding-left: 10px; }
  .approach li.sq::before { content: ""; position: absolute; left: 0; top: 4.5px; width: 3.5px; height: 3.5px; background: var(--green); }
  .approach-sub { left: 410px; top: 853px; font-size: 8.6px; font-weight: 600; color: var(--green); text-decoration: underline; }

  .partners { left: 0; top: 1045px; width: 865px; height: 85px; background: var(--panel); }
  .partner { position: absolute; top: 28px; height: 32px; display: flex; align-items: center; justify-content: center; gap: 5px; font-size: 9px; font-weight: 700; color: #333; background: var(--white); }
  .partner i { width: 8px; height: 8px; background: #333; display: block; }

  .footer { left: 0; top: 1130px; width: 865px; height: 70px; background: var(--green-dark); }
  .copyright { left: 136px; top: 31px; font-size: 7.2px; color: var(--white); }
  .social { left: 623px; top: 26px; display: flex; gap: 6px; }
  .social span { width: 16px; height: 16px; border-radius: 50%; background: #e6eee6; display: block; }
</style>
</head>
<body>

<header>
  <div class="abs brand">
    <div class="brand-name">Dunmore Kestrel</div>
  </div>
  <div class="abs phone">
    <svg width="16" height="13" viewBox="0 0 16 13" aria-hidden="true">
      <path d="M1 4 Q8 -1 15 4 L13 6 L11 4.5 L5 4.5 L3 6 Z" fill="#1f6a1b"/>
      <rect x="3" y="6" width="10" height="6.5" rx="1" fill="#1f6a1b"/>
      <circle cx="8" cy="9.2" r="2" fill="#fff"/>
    </svg>
    <span>917-555-0183</span>
  </div>
</header>

<nav class="abs nav">
  <ul>
    <li>HOME</li>
    <li>ABOUT US</li>
    <li>SERVICES</li>
    <li>REPRESENTATIVE ENGAGEMENTS</li>
    <li>GLOBAL SCOPE AND PERSPECTIVE</li>
    <li>BIOS</li>
    <li>CONTACT US</li>
  </ul>
</nav>

<section>
  <div class="abs hero" role="img" aria-label="Smoky industrial photo of a worker pointing beside heavy steel machinery and ropes"></div>
  <p class="abs hero-caption">One of the world’s premier financial advisors to the steel, metals and mining industries.</p>
  <div class="abs hero-dots"><span></span><span></span><span></span></div>
</section>

<section class="abs welcome">
  <h2 class="h2"><em>Welcome to</em> Dunmore Kestrel</h2>
  <div class="abs welcome-photo" role="img" aria-label="Photo of stacked steel pipes with a worker on top"></div>
  <div class="abs welcome-rule"></div>
  <div class="abs welcome-text">
    <p>Dunmore Kestrel is led by Edward L. Dunmore, Chairman and CEO, who has over 35 years of professional experience</p>
    <p>Mr. Dunmore is supported by a skilled professional staff</p>
    <p>Since its formation in 2003, Dunmore Kestrel has been widely recognized as the #1 independent financial advisor to the global steel, metals and mining sector</p>
    <p>We are international in scope, representing companies all around the world. This gives us a true global perspective within our sector</p>
    <p>We specialize in:</p>
    <p>Sell-side engagements for companies and projects</p>
    <p>Finding Strategic or Financial partners/investors for worthy companies and projects</p>
  </div>
</section>

<section>
  <h2 class="abs h2 services-title"><em>Our</em> Services</h2>
  <p class="abs services-copy">Morbi interdum mollis sapien. Sed ac risus. Phasellus lacinia, magna a ullamcorper laoreet, lectus arcu pulvinar risus, vitae facilisis libero dolor a purus. Sed vel lacus. Mauris nibh felis, adipiscing varius, adipiscing in, lacinia vel, tellus. Suspendisse ac urna. Etiam pellentesque mauris ut lectus. Nunc tellus ante, mattis eget, gravida vitae, ultricies ac, leo. Integer leo pede</p>
  <ul class="abs services-list">
    <li><svg width="6" height="8" viewBox="0 0 6 8" aria-hidden="true"><path d="M1 0.5 L5 4 L1 7.5" stroke="#0f5212" stroke-width="1.8" fill="none"/></svg>STRATEGIC ADVICE</li>
    <li><svg width="6" height="8" viewBox="0 0 6 8" aria-hidden="true"><path d="M1 0.5 L5 4 L1 7.5" stroke="#0f5212" stroke-width="1.8" fill="none"/></svg>MERGERS &amp;ACQUISITIONS</li>
    <li><svg width="6" height="8" viewBox="0 0 6 8" aria-hidden="true"><path d="M1 0.5 L5 4 L1 7.5" stroke="#0f5212" stroke-width="1.8" fill="none"/></svg>CAPITALRAISING</li>
    <li><svg width="6" height="8" viewBox="0 0 6 8" aria-hidden="true"><path d="M1 0.5 L5 4 L1 7.5" stroke="#0f5212" stroke-width="1.8" fill="none"/></svg>STRATEGIC/FINANCIAL PARTNERS</li>
  </ul>
  <span class="abs btn" style="left:134px;top:733px;">Read more</span>
  <div class="abs services-photo" role="img" aria-label="Photo of bundled steel reinforcing bars"></div>
</section>

<div class="abs divider"></div>

<section>
  <h2 class="abs h2 articles-title"><em>Dunmore Kestrel</em> Articles</h2>
  <article class="abs article" style="top:814px;">
    <h3>China to look beyond borders for acquisitions</h3>
    <div class="date">June 29, 2009</div>
    <p>China is almost certain to look beyond its borders to strengthen its role in the international steel market once political and procedural considerations</p>
  </article>
  <div class="abs dots"></div>
  <article class="abs article" style="top:899px;">
    <h3>Soaring Steel Makes Winners and Losers</h3>
    <div class="date">April 24, 2004</div>
    <p>Recently the prices of several key steelmaking raw materials have gone through the roof. Since the end of 2003, the price of iron ore has soared 321%, and it’s up 65% just in the last year.</p>
  </article>
  <span class="abs btn" style="left:136px;top:996px;">Read more</span>

  <h2 class="abs h2 approach-title"><em>Our</em> Approach</h2>
  <ul class="abs approach" style="top:817px;">
    <li class="sq">In analyzing a new project or opportunity Dunmore Kestrel takes a deep, substantive approach</li>
    <li class="sq">We try to put ourselves in the position of a buyer/investor in the project</li>
  </ul>
  <div class="abs approach-sub">Metals and Mining</div>
  <ul class="abs approach" style="top:867px;">
    <li class="sq">In metals and mining we analyze:</li>
    <li>Global and regional supply/demand profile and outlook for the resource</li>
    <li class="sq">Global competitors</li>
    <li class="sq">Location of the project, including country political and economic stability and risk profile</li>
    <li class="sq">Native people issues</li>
    <li class="sq">Ability to obtain exploration and mining permits and the time frame for the same</li>
    <li class="sq">Quantity and quality of the resource</li>
    <li class="sq">Whether a JORC or Ni 43-101 Report is available</li>
    <li class="sq">Ex-mine cost</li>
  </ul>
  <span class="abs btn" style="left:403px;top:996px;">Read more</span>
</section>

<section class="abs partners">
  <svg class="abs" style="left:84px;top:30px;" width="14" height="26" viewBox="0 0 14 26" aria-hidden="true"><path d="M12 1 L2 13 L12 25" stroke="#c9c9c9" stroke-width="3" fill="none"/></svg>
  <div class="partner" style="left:137px;width:85px;"><i></i>Velmora Steel</div>
  <div class="partner" style="left:237px;width:110px;">Hanlin River Steel</div>
  <div class="partner" style="left:358px;width:102px;background:#666;color:#fff;">Corvane</div>
  <div class="partner" style="left:471px;width:108px;">Pellham</div>
  <div class="partner" style="left:593px;width:48px;top:22px;height:40px;">Tessaro</div>
  <div class="partner" style="left:657px;width:69px;top:34px;height:16px;background:#333;color:#fff;">Brenmark</div>
  <svg class="abs" style="left:764px;top:30px;" width="14" height="26" viewBox="0 0 14 26" aria-hidden="true"><path d="M2 1 L12 13 L2 25" stroke="#c9c9c9" stroke-width="3" fill="none"/></svg>
</section>

<footer class="abs footer">
  <p class="abs copyright">Copyright © 2014 Dunmore Kestrel Group Inc. (An Affiliate of  Broker Dealer Related Services Provided)</p>
  <div class="abs social"><span></span><span></span><span></span><span></span></div>
</footer>

</body>
</html>
```